Naturopath Practitioner Card Design

I am a naturopath needing a design for a business card mainly to show that I am a naturopath and have some contact details to give to prospective clients. I am open minded about the design and what is on the second side of the card whether it just be some artwork or space for details, appointment times etc. Naturopathy is the practice of natural medicine that uses a holistic approach and incorporates herbal and nutritional medicine.

Industry/Entity Type

Business

Contact Information for Business Card

Tom Rudd NaturopathBHSc (Naturopathy) Member WHPG 0487 925 316 tom.rudd@mailexample.com www.tomruddnaturopathy.example.au

Requirements
Nice to have
• Would prefer some kind of original pattern/art work/logo rather than an image, not fussed if its very simple/basic
• I am open to any colour but think I would prefer a more earthy sandy clay etc type style than the greens that are commonly associated with naturopathy.
Should not have
• Don't really want to have generic stock images on it

```html
<!DOCTYPE html>
<html lang="en">
<head>
<meta charset="utf-8">
<title>Tom Rudd Naturopathy – Business Card</title>
<link href="https://fonts.googleapis.com/css2?family=Cinzel:wght@400&family=Open+Sans:wght@400;600&display=swap" rel="stylesheet">
<style>
  :root{
    --backdrop:#e8e4dd;
    --card:#ffffff;
    --sage:#6b8a3a;
    --ink:#3a3a3c;
    --text:#333333;
    --rule:#c9c9c9;
  }
  *{box-sizing:border-box;margin:0;padding:0}
  html,body{width:1200px;height:1000px;overflow:hidden}
  body{background:var(--backdrop);position:relative;font-family:"Open Sans",Arial,sans-serif}
  .card{
    position:absolute;left:265px;width:666px;height:397px;
    background:var(--card);box-shadow:0 3px 10px rgba(0,0,0,.18);overflow:hidden;
  }
  .card--front{top:73px}
  .card--back{top:532px}
  .brand{
    position:absolute;left:0;right:0;text-align:center;
    font-family:"Cinzel",Georgia,serif;font-weight:400;color:var(--ink);
  }
  .brand__mark{
    display:block;margin:0 auto 14px;width:46px;height:46px;border-radius:50%;background:var(--sage);
  }
  .brand__name{display:block;font-size:54px;line-height:1;letter-spacing:1px}
  .brand__trade{display:block;font-size:23px;line-height:1;letter-spacing:1.5px;margin-top:8px}
  .card--front .brand{top:82px}
  .card--back .brand{top:128px}
  .card--back .brand__name{font-size:62px}
  .card--back .brand__trade{font-size:27px;margin-top:10px}
  .credentials{position:absolute;top:266px;left:0;right:0;text-align:center;color:var(--sage)}
  .credentials__name{font-weight:600;font-size:19px}
  .credentials__degree{font-size:16px}
  .credentials__rule{
    width:240px;height:1px;margin:5px auto 6px;
    background:linear-gradient(90deg,transparent,var(--rule),transparent);
  }
  .credentials__member{color:var(--text);font-size:15px}
  .contact{
    position:absolute;top:338px;left:24px;right:24px;
    display:flex;flex-wrap:nowrap;justify-content:center;gap:14px;
    font-size:14px;color:var(--text);
  }
  .contact__item{display:flex;align-items:center;gap:5px;white-space:nowrap;flex:none}
  .contact__icon{width:13px;height:13px;fill:var(--sage);flex:none}
  .band{position:absolute;left:0;right:0;bottom:0;height:24px;background:var(--sage)}
</style>
</head>
<body>
  <section class="card card--front">
    <div class="brand">
      <span class="brand__mark"></span>
      <span class="brand__name">Tom Rudd</span>
      <span class="brand__trade">Naturopathy</span>
    </div>
    <div class="credentials">
      <p><span class="credentials__name">Tom Rudd</span> <span class="credentials__degree">BHSc (Naturopathy)</span></p>
      <div class="credentials__rule"></div>
      <p class="credentials__member">Member WHPG</p>
    </div>
    <div class="contact">
      <span class="contact__item">
        <svg class="contact__icon" viewBox="0 0 16 16" aria-hidden="true"><rect x="1" y="3" width="14" height="10"/><path d="M1 3l7 6 7-6" fill="none" stroke="#fff" stroke-width="1.2"/></svg>
        tom.rudd@mailexample.com
      </span>
      <span class="contact__item">
        <svg class="contact__icon" viewBox="0 0 16 16" aria-hidden="true"><path d="M4 1l3 3-2 2c1 2 3 4 5 5l2-2 3 3-2 3C7 15 1 9 1 3z"/></svg>
        0487 925 316
      </span>
      <span class="contact__item">
        <svg class="contact__icon" viewBox="0 0 16 16" aria-hidden="true"><circle cx="8" cy="8" r="7"/><path d="M1 8h14M8 1c3 3 3 11 0 14M8 1c-3 3-3 11 0 14" stroke="#fff" stroke-width="1" fill="none"/></svg>
        www.tomruddnaturopathy.example.au
      </span>
    </div>
    <div class="band"></div>
  </section>

  <section class="card card--back">
    <div class="brand">
      <span class="brand__mark"></span>
      <span class="brand__name">Tom Rudd</span>
      <span class="brand__trade">Naturopathy</span>
    </div>
  </section>
</body>
</html>
```